Business Cards

Need business card design that I can update for new employees and details. Needs to incorporate our logo, be bright and fun (in line with tourism and holidays)
Would like a Map of Western Australia on the front with locations all the caravan parks we own (just purchased Tom Price so please include that as well as others listed on our website).
Target Market(s)
Famillies
Contact Information for Business Card
5 Cards -
Neil Perrow (Director) e: perrow@wattlebay.com.au p: 0491 570 156
Mira Perrow (Director) e: perrow@wattlebay.com.au p: 0491 570 157
Owen Halvey (General Manager) e: halvey@wattlebay.com.au p: 0491 570 158
Helen Halvey (General Manager) e: halvey@wattlebay.com.au p: 0491 570 159
Colin Danby (Training and Operations Manager) - e: danby@wattlebay.com.au p:0491 570 110
Colors
Look and feel

```html
<!DOCTYPE html>
<html lang="en">
<head>
<meta charset="utf-8">
<title>Wattlebay Tourist Parks – Business Card</title>
<link rel="stylesheet" href="https://fonts.googleapis.com/css2?family=Cormorant+Garamond:wght@500;600&family=PT+Sans:wght@400&display=swap">
<style>
  :root {
    --stage: #212121;
    --card-white: #ffffff;
    --teal: #3dbcc9;
    --teal-text: #29b3c2;
    --sea-green: #6dbcae;
    --ink: #4a4a4a;
    --ink-dark: #222222;
    --white: #ffffff;
  }
  * { margin: 0; padding: 0; box-sizing: border-box; }
  html, body {
    width: 1200px;
    height: 900px;
    overflow: hidden;
    background: var(--stage);
  }
  .stage {
    position: relative;
    width: 1200px;
    height: 900px;
  }
  .card {
    position: absolute;
    top: 306px;
    width: 440px;
    height: 271px;
    overflow: hidden;
  }
  .card--front {
    left: 149px;
    background: var(--card-white);
  }
  .card--back {
    left: 608px;
    width: 441px;
    height: 272px;
    background: linear-gradient(150deg, var(--teal) 0%, var(--sea-green) 50%, var(--teal) 100%);
  }

  /* Brand lockup on the front */
  .brand {
    position: absolute;
    left: 23px;
    top: 41px;
    display: flex;
    align-items: center;
    gap: 7px;
  }
  .brand__mark {
    width: 58px;
    height: 58px;
    background: var(--teal);
    border: 2px solid var(--white);
    outline: 1.5px solid var(--teal);
  }
  .brand__words {
    font-family: "Cormorant Garamond", serif;
    font-weight: 600;
    color: var(--ink);
    text-align: center;
    line-height: 1;
  }
  .brand__name {
    font-size: 24px;
    letter-spacing: 2.5px;
    display: block;
  }
  .brand__tagline {
    font-size: 11px;
    letter-spacing: 2px;
    display: block;
    margin-top: 3px;
  }

  /* Person details */
  .person {
    position: absolute;
    left: 24px;
    top: 151px;
  }
  .person__name {
    font-family: "Cormorant Garamond", serif;
    font-weight: 600;
    font-size: 20px;
    letter-spacing: 0.3px;
    color: var(--teal-text);
    line-height: 1;
  }
  .person__role {
    font-family: "PT Sans", sans-serif;
    font-size: 12px;
    color: var(--ink-dark);
    margin-top: 4px;
  }
  .contact {
    position: absolute;
    left: 23px;
    top: 203px;
    list-style: none;
    font-family: "PT Sans", sans-serif;
    font-size: 13.5px;
    color: var(--ink-dark);
  }
  .contact__item {
    display: flex;
    align-items: center;
    gap: 6px;
    height: 21px;
  }
  .contact__icon {
    width: 16px;
    height: 16px;
    flex: none;
  }

  /* Back of card */
  .back-lockup {
    position: absolute;
    left: 0;
    right: 0;
    top: 65px;
    text-align: center;
    color: var(--white);
    font-family: "Cormorant Garamond", serif;
    font-weight: 600;
  }
  .back-lockup__mark {
    width: 92px;
    height: 91px;
    margin: 0 auto;
    border: 2px solid var(--white);
    box-shadow: inset 0 0 0 3px transparent, inset 0 0 0 4px var(--white);
  }
  .back-lockup__name {
    display: block;
    font-size: 36px;
    letter-spacing: 5px;
    line-height: 1;
    margin-top: 12px;
  }
  .back-lockup__tagline {
    display: block;
    font-size: 16px;
    letter-spacing: 3.5px;
    margin-top: 5px;
  }
</style>
</head>
<body>
<main class="stage">

  <section class="card card--front" aria-label="Business card front">
    <div class="brand">
      <div class="brand__mark"></div>
      <div class="brand__words">
        <span class="brand__name">WATTLEBAY</span>
        <span class="brand__tagline">TOURIST PARKS</span>
      </div>
    </div>

    <div class="person">
      <h1 class="person__name">NEIL PERROW</h1>
      <p class="person__role">Director</p>
    </div>

    <ul class="contact">
      <li class="contact__item">
        <svg class="contact__icon" viewBox="0 0 16 16" aria-hidden="true">
          <rect width="16" height="16" rx="1.5" fill="var(--teal)"/>
          <path d="M5 3.2c.5-.3 1-.2 1.3.3l.9 1.6c.2.4.1.9-.3 1.2l-.6.4c.4 1.2 1.3 2.2 2.5 2.7l.4-.6c.3-.4.8-.5 1.2-.3l1.6.9c.5.3.6.9.3 1.3l-.6.8c-.4.5-1.1.7-1.7.5C7.3 11.2 4.8 8.7 4 5.9c-.2-.6 0-1.3.5-1.7z" fill="var(--white)"/>
        </svg>
        <span>0491 570 156</span>
      </li>
      <li class="contact__item">
        <svg class="contact__icon" viewBox="0 0 16 16" aria-hidden="true">
          <rect width="16" height="16" rx="1.5" fill="var(--teal)"/>
          <rect x="3" y="4.5" width="10" height="7" fill="none" stroke="var(--white)" stroke-width="1.2"/>
          <path d="M3 4.5 8 8.6 13 4.5" fill="none" stroke="var(--white)" stroke-width="1.2"/>
        </svg>
        <span>perrow@wattlebay.com.au</span>
      </li>
    </ul>
  </section>

  <section class="card card--back" aria-label="Business card back">
    <div class="back-lockup">
      <div class="back-lockup__mark"></div>
      <span class="back-lockup__name">WATTLEBAY</span>
      <span class="back-lockup__tagline">TOURIST PARKS</span>
    </div>
  </section>

</main>
</body>
</html>
```